CoinHarbor.com Site Redesign

We are looking to redesign our CoinHarbor.com site. This site is focused on helping consumers make smart financial decisions. We provide reviews and articles in various categories.

We are looking for a responsive design to run on wordpress. We will also have adsense advertisements on our page and will want some ad spot space. We are thinking of two column design vs. single column.

Here is an example of what our competitors look like:
ShopperBeacon.org (mostly reviews vs. articles)
Homepage - https://www.shopperbeacon.example/
Category Review Listing - https://www.shopperbeacon.example/mortgage-refinance/best-mortgage-refinance
Individual Review - https://www.shopperbeacon.example/mortgage-refinance/c/loan-orchard-mortgage-refinance-review

- I like that the site is extremely clean. I like the fixed header in mobile

PilotGuide
Homepage - https://www.pilotguide.example/
Category Review Listing-https://www.pilotguide.example/auto_insurance/index.php
Individual Review- https://www.pilotguide.example/auto_insurance/drivora_review.php

Articles - https://www.pilotguide.example/blog/2017/11/20/going-on-a-holiday-road-trip-be-prepared-for-these-hazards/

What I Like? I like the two column layout in that it gives room for advertising.
What I Do NOT Like? The top navigation is a little cumbersome and old. Mobile view is not very good. Content seems a bit cluttered.

PennyMoth
Homepage - https://www.pennymoth.example
Category Review Listing - https://www.pennymoth.example/blog/insurance/best-car-insurance-companies/?trk=pm_gn1_4.0
Individual Review- https://www.pennymoth.example/blog/insurance/veloro-insurance-review/

What I Like? very clean. Like the use of white space and focus on bright color call to action buttons.
What I Do NOT Like? In mobile a lot of content is pushed below the fold because of the large image above the fold. Reviews are not well organized.

Target Market(s)

consumers interested in saving money and making smart financial decisions

Industry/Entity Type

Financial

Logo Text

CoinHarbor.com or CoinHarbor

Coding

Coded - Design and coding required

Number of Pages Required

5+ page

Font styles to use
Sans Serif

Colors

Designer to choose colors to be used in the design.

Requirements
Must have
• -responsive design
• -room for ad space in the right column
Nice to have
• -good use of white space
• -clean layouts
Should not have
• -clutter

```html
<!DOCTYPE html>
<html lang="en">
<head>
<meta charset="utf-8">
<title>CoinHarbor.com — Make smarter financial decisions</title>
<link rel="stylesheet" href="https://fonts.googleapis.com/css2?family=Roboto:wght@400;500;700&family=Signika:wght@600;700&display=swap">
<style>
:root{
  --navy:#0b3a8e;
  --navy-light:#1d5bb3;
  --teal:#1a86b8;
  --ink:#2b2b2b;
  --muted:#8c8c8c;
  --line:#d9d9d9;
  --panel:#f7f7f7;
  --footer:#1e1e1e;
  --ad-yellow:#f6ec2a;
  --link-blue:#1a4f9c;
  --white:#ffffff;
}
*{box-sizing:border-box;margin:0;padding:0}
html,body{width:1200px;height:2469px;overflow:hidden;background:var(--white)}
body{font-family:"Roboto",Arial,sans-serif;color:var(--ink);position:relative}
a{color:inherit;text-decoration:none}

/* Top bar */
.topbar{height:95px;position:relative}
.brand{position:absolute;left:99px;top:34px;display:flex;align-items:center;gap:10px;font-weight:700;font-size:22px;color:var(--navy)}
.brand-mark{width:26px;height:26px;background:var(--navy);border-radius:3px}
.topbar-links{position:absolute;top:40px;font-size:14px;color:#555}
.cat-select{left:588px}
.cat-select::after{content:"";display:inline-block;margin-left:10px;border:5px solid transparent;border-top-color:#555;transform:translateY(3px)}
.login{left:736px}
.signup{left:818px}
.social{position:absolute;left:895px;top:32px;display:flex;gap:6px}
.social span{width:36px;height:36px;border-radius:50%;background:var(--navy)}
.social span:nth-child(2n){background:var(--navy-light)}

/* Nav */
.mainnav{height:45px;background:var(--navy);position:relative}
.nav-home{position:absolute;left:100px;top:0;width:53px;height:45px;background:var(--navy-light);display:flex;align-items:center;justify-content:center}
.nav-link{position:absolute;top:15px;font-size:13px;color:var(--white);font-weight:500}

/* Hero */
.hero{position:relative;height:406px;background:linear-gradient(120deg,#2b3f66 0%,#4a5a85 35%,#6b4a63 60%,#2f4470 100%);text-align:center;color:var(--white)}
.hero h1{position:absolute;left:0;right:0;top:92px;font-family:"Signika",Arial,sans-serif;font-weight:700;font-size:50px;text-shadow:0 2px 6px rgba(0,0,0,.35)}
.hero .sub{position:absolute;left:0;right:0;top:165px;font-size:21px;font-weight:500;letter-spacing:.5px}
.hero .disclosure{position:absolute;left:0;right:0;top:210px;font-size:11px}
.search{position:absolute;left:263px;top:257px;width:672px;height:43px;background:var(--white);border-radius:22px;display:flex;overflow:hidden;box-shadow:0 0 0 2px rgba(255,255,255,.6)}
.search .field{flex:1;text-align:left;padding:13px 23px;font-size:14px;color:#777}
.search .btn{width:134px;background:var(--teal);color:var(--white);font-weight:700;font-size:17px;display:flex;align-items:center;justify-content:center;letter-spacing:.5px}

/* Content */
.content{position:absolute;top:620px;left:0;width:1200px}
.section-title{position:absolute;left:97px;top:0;font-size:32px;font-weight:400;color:#222}
.pager{position:absolute;left:740px;top:8px;display:flex;gap:9px}
.pager span{width:24px;height:24px;border-radius:50%;background:#d4d4d4;display:flex;align-items:center;justify-content:center}
.grid{position:absolute;left:99px;top:76px;width:697px;display:grid;grid-template-columns:repeat(3,225px);grid-auto-rows:200px;gap:10px 11px}
.tile{display:flex;align-items:center;justify-content:center;text-align:center;color:var(--white);font-weight:700;font-size:20px;text-shadow:0 1px 4px rgba(0,0,0,.6);padding:0 20px;line-height:1.4}
.t-ann{background:linear-gradient(160deg,#3f74b5,#2a5a9a)}
.t-auto{background:linear-gradient(160deg,#8b7a5e,#3c3326)}
.t-cred{background:linear-gradient(160deg,#5a5048,#2c2a28)}
.t-repair{background:linear-gradient(160deg,#4a4a4e,#222226)}
.t-debt{background:linear-gradient(160deg,#6a6660,#3a3936)}
.t-id{background:linear-gradient(160deg,#77777a,#38383b)}
.t-life{background:linear-gradient(160deg,#3e3d42,#18181b)}
.t-mort{background:linear-gradient(160deg,#6e6b62,#3f4a3a)}
.t-broke{background:linear-gradient(160deg,#7d8aa0,#3b4a66)}
.t-pay{background:linear-gradient(160deg,#a09a92,#4a4642)}
.t-pers{background:linear-gradient(160deg,#b23a33,#6d6a70)}
.t-student{background:linear-gradient(160deg,#c9c9c9,#6e6e6e)}

/* Sidebar */
.sidebar{position:absolute;left:843px;top:9px;width:257px}
.ad-slot{height:214px}
.ad-game{background:linear-gradient(160deg,#e8b24a,#7d3a1c 60%,#2b1a10)}
.ad-tips{margin-top:16px;background:var(--ad-yellow)}
.recent{margin-top:17px;height:438px;background:var(--panel);border:1px solid var(--line);padding:25px 21px}
.recent h3{font-size:21px;font-weight:400;color:#333}
.recent .rule{width:70px;height:3px;background:var(--teal);margin:12px 0 20px}
.recent a{display:block;font-size:14.5px;line-height:25px;color:#666;text-decoration:underline;margin-bottom:14px}
.recent a:first-of-type{color:var(--link-blue)}

.divider{position:absolute;left:99px;top:1611px;width:1001px;height:4px;background:#e2e2e2}

/* About */
.about{position:absolute;top:1688px;left:0;width:1200px;text-align:center}
.about h2{font-size:32px;font-weight:400;color:#222}
.about .tag{margin-top:14px;font-size:16px;color:var(--muted)}
.features{position:absolute;top:114px;left:100px;display:flex;gap:24px}
.feature{width:317px;height:224px;border:1px solid var(--line);background:var(--white);padding-top:27px}
.feature.is-active{background:var(--navy);border-color:var(--navy);color:var(--white)}
.feature .icon{display:block;width:82px;height:82px;margin:0 auto}
.feature h4{margin-top:24px;font-size:16px;font-weight:700}
.feature p{margin:14px auto 0;width:240px;font-size:12.5px;line-height:1.7;color:#777}
.feature.is-active p{color:var(--white);width:300px;font-size:12px}

/* Footer */
.footer{position:absolute;top:2109px;left:0;width:1200px;height:360px;background:var(--footer);color:var(--white);text-align:center}
.footer .social{position:static;justify-content:center;margin-top:75px;gap:14px}
.footer .social span{width:46px;height:46px}
.footer nav{margin-top:25px;font-size:14px;display:flex;justify-content:center;gap:22px}
.footer nav span{color:#bbb}
.footer .motto{margin-top:30px;font-size:27px}
.footer .copy{margin-top:24px;font-size:11.5px}
</style>
</head>
<body>

<header class="topbar">
  <a class="brand" href="#"><span class="brand-mark"></span>CoinHarbor.com</a>
  <span class="topbar-links cat-select">All Categories</span>
  <a class="topbar-links login" href="#">Login</a>
  <a class="topbar-links signup" href="#">Sign Up</a>
  <div class="social" aria-label="Social links"><span></span><span></span><span></span><span></span><span></span></div>
</header>

<nav class="mainnav">
  <a class="nav-home" href="#" aria-label="Home">
    <svg width="22" height="20" viewBox="0 0 22 20"><path d="M11 1 1 10h3v9h5v-6h4v6h5v-9h3z" fill="#fff"/></svg>
  </a>
  <a class="nav-link" href="#" style="left:189px">ANNUITIES</a>
  <a class="nav-link" href="#" style="left:309px">AUTO INSURANCE</a>
  <a class="nav-link" href="#" style="left:471px">CREDIT MONITORING</a>
  <a class="nav-link" href="#" style="left:650px">DEBT MANAGEMENT</a>
  <a class="nav-link" href="#" style="left:828px">MORTGAGES</a>
</nav>

<section class="hero" role="img" aria-label="Financial charts and rising arrow over stacked books">
  <h1>Make smarter Financial decisions</h1>
  <p class="sub">FIND THE BEST FINANCIAL PRODUCTS &amp; SERVICES</p>
  <p class="disclosure">Disclosure: We receive advertising revenue from some partners. Learn more.</p>
  <div class="search"><span class="field">Product Category</span><span class="btn">SEARCH</span></div>
</section>

<main class="content">
  <h2 class="section-title">Product Category</h2>
  <div class="pager">
    <span><svg width="12" height="12" viewBox="0 0 12 12"><path d="M8 2 4 6l4 4" stroke="#fff" stroke-width="2" fill="none"/></svg></span>
    <span><svg width="12" height="12" viewBox="0 0 12 12"><path d="M4 2l4 4-4 4" stroke="#fff" stroke-width="2" fill="none"/></svg></span>
  </div>
  <div class="grid">
    <a class="tile t-ann" role="img" aria-label="Annuities photo">Annuities</a>
    <a class="tile t-auto" role="img" aria-label="Auto insurance photo">Auto Insurance</a>
    <a class="tile t-cred" role="img" aria-label="Credit monitoring photo">Credit Monitoring</a>
    <a class="tile t-repair" role="img" aria-label="Credit repair photo">Credit Repair</a>
    <a class="tile t-debt" role="img" aria-label="Debt management photo">Debt Management</a>
    <a class="tile t-id" role="img" aria-label="Identity theft photo">Identity Theft</a>
    <a class="tile t-life" role="img" aria-label="Life insurance photo">Life Insurance</a>
    <a class="tile t-mort" role="img" aria-label="Mortgages photo">Mortgages</a>
    <a class="tile t-broke" role="img" aria-label="Online brokerages photo">Online Brokerages</a>
    <a class="tile t-pay" role="img" aria-label="Payday loans photo">Payday Loans</a>
    <a class="tile t-pers" role="img" aria-label="Personal finance photo">Personal Finance</a>
    <a class="tile t-student" role="img" aria-label="Student loan consolidation photo">Student Loan Consolidation</a>
  </div>

  <aside class="sidebar">
    <div class="ad-slot ad-game" role="img" aria-label="Advertisement space: card game banner"></div>
    <div class="ad-slot ad-tips" role="img" aria-label="Advertisement space: stock tips trial banner"></div>
    <div class="recent">
      <h3>Recent Articles</h3>
      <div class="rule"></div>
      <a href="#">5 “Easy” Ways Parents Can Save $1000’s a Year</a>
      <a href="#">Motorcycle Insurance Basics</a>
      <a href="#">How Do I Get Cheap Auto Insurance?</a>
      <a href="#">LA Car Insurance Requirements</a>
      <a href="#">How Do I Buy General Auto Insurance?</a>
      <a href="#">How to Shop for Young Driver’s Insurance?</a>
    </div>
  </aside>
</main>

<div class="divider"></div>

<section class="about">
  <h2>What is CoinHarbor.com?</h2>
  <p class="tag">Financial Service Advice and Reviews</p>
  <div class="features">
    <div class="feature is-active">
      <svg class="icon" viewBox="0 0 82 82" role="img" aria-label="Analysis icon"><circle cx="41" cy="41" r="41" fill="#f2a51f"/><rect x="20" y="24" width="42" height="32" rx="3" fill="#fff"/><circle cx="38" cy="40" r="8" fill="none" stroke="#1d5bb3" stroke-width="3"/><path d="M44 46l7 7" stroke="#1d5bb3" stroke-width="3"/></svg>
      <h4>We Analyze &amp; Explain</h4>
      <p>We analyze &amp; explain how each online service works</p>
    </div>
    <div class="feature">
      <svg class="icon" viewBox="0 0 82 82" role="img" aria-label="Testing gauge icon"><circle cx="41" cy="41" r="41" fill="#d9342b"/><rect x="20" y="24" width="42" height="32" rx="3" fill="#fff"/><circle cx="41" cy="41" r="9" fill="none" stroke="#333" stroke-width="2.5"/><path d="M41 41v-6" stroke="#333" stroke-width="2.5"/></svg>
      <h4>We Test &amp; Compare</h4>
      <p>We test &amp; compare the leading services in each category</p>
    </div>
    <div class="feature">
      <svg class="icon" viewBox="0 0 82 82" role="img" aria-label="Rating icon"><circle cx="41" cy="41" r="41" fill="#2fb08a"/><path d="M26 42l10 10 20-22" stroke="#fff" stroke-width="5" fill="none"/></svg>
      <h4>We Review &amp; Rate</h4>
      <p>We review and rate each service to show which is best</p>
    </div>
  </div>
</section>

<footer class="footer">
  <div class="social" aria-label="Social links"><span></span><span></span><span></span><span></span></div>
  <nav>
    <a href="#">HOME</a><span>/</span>
    <a href="#">ANNUITIES</a><span>/</span>
    <a href="#">AUTO INSURANCE</a><span>/</span>
    <a href="#">CREDIT MONITORING</a><span>/</span>
    <a href="#">DEBT MANAGEMENT</a><span>/</span>
    <a href="#">MORTGAGES</a>
  </nav>
  <p class="motto">Trusted Financial Advice and Reviews Since 2001</p>
  <p class="copy">Copyright © 2017,CoinHarbor.All rights reserved.</p>
</footer>

</body>
</html>
```